Upmarket Dessert Lounge needs a Business Card Design

We are an upmarket dessert lounge needing a business card to match our image.

We want something that is simple yet beautiful, feminine, classy, sophisticated and elegant. We want it to stand out and don't mind if it is bold.

The design should include our logo and colours of red or maroon with gold highlights. We don't mind if black is used.

Marlow & Quince

Target Market(s)

For those who like to indulge or treat themselves and give in to their temptations on good quality desserts.

Industry/Entity Type

Business

Requirements
Must have
• Must include our logo and our name

Marlow & Quince

M & Q

```html
<!DOCTYPE html>
<html lang="en">
<head>
<meta charset="utf-8">
<title>Marlow &amp; Quince — Business Card</title>
<link rel="stylesheet" href="https://fonts.googleapis.com/css2?family=Libre+Baskerville:wght@400;700&family=Lato:wght@400&display=swap">
<style>
  :root {
    --maroon-deep: #5e0e0e;
    --maroon: #8e1b1b;
    --maroon-light: #a8302b;
    --gold: #e9b77f;
    --gold-soft: #f4c993;
    --paper: #ffffff;
    --ink: #2a1a1a;
    --backdrop: #d9d6d2;
  }
  * { box-sizing: border-box; margin: 0; padding: 0; }
  html, body { width: 1200px; height: 951px; overflow: hidden; }
  body { background: var(--backdrop); position: relative; font-family: "Libre Baskerville", Georgia, serif; }

  .card {
    position: absolute;
    width: 620px;
    height: 354px;
    border-radius: 22px;
    overflow: hidden;
    box-shadow: 0 12px 30px rgba(0,0,0,0.28);
  }

  /* Front */
  .card--front {
    left: 70px; top: 70px;
    background: radial-gradient(ellipse at 45% 45%, var(--maroon-light) 0%, var(--maroon) 45%, var(--maroon-deep) 100%);
  }
  .front__ornament {
    position: absolute; right: 0; top: 0;
    width: 300px; height: 110px;
    background: radial-gradient(ellipse at 80% 20%, rgba(233,183,127,0.55), rgba(233,183,127,0) 70%);
  }
  .front__name {
    position: absolute; left: 0; right: 0; top: 142px;
    text-align: center;
    font-size: 34px; font-weight: 700; letter-spacing: 1px;
    color: var(--gold);
  }
  .front__web {
    position: absolute; left: 0; right: 0; bottom: 34px;
    text-align: center;
    font-size: 17px; font-weight: 700;
    color: var(--paper);
  }

  /* Back */
  .card--back {
    left: 510px; top: 527px;
    background: var(--paper);
  }
  .back__band { position: absolute; inset: 0; }
  .back__ornament {
    position: absolute; right: 10px; top: 10px;
    width: 260px; height: 150px;
    background: radial-gradient(ellipse at 60% 35%, rgba(233,183,127,0.5), rgba(233,183,127,0) 70%);
  }
  .back__name {
    position: absolute; left: 36px; top: 110px;
    font-size: 19px; font-weight: 700;
    color: var(--maroon);
  }
  .contact-list {
    position: absolute; left: 36px; top: 218px;
    list-style: none;
    font-size: 14.5px; color: var(--ink); line-height: 22px;
  }
  .contact-list li { display: flex; align-items: center; gap: 10px; }
  .contact-list svg { width: 14px; height: 14px; flex: none; }
  .back__signature {
    position: absolute; right: 34px; bottom: 30px;
    font-family: "Lato", Arial, sans-serif;
    font-size: 22px; color: var(--maroon);
  }
</style>
</head>
<body>

<section class="card card--front" aria-label="Business card front">
  <div class="front__ornament" role="img" aria-label="Gold floral flourish in the corner"></div>
  <div class="front__name">Marlow &amp; Quince</div>
  <div class="front__web">www.marlowquince.com</div>
</section>

<section class="card card--back" aria-label="Business card back">
  <svg class="back__band" viewBox="0 0 620 354" preserveAspectRatio="none" aria-hidden="true">
    <defs>
      <linearGradient id="bandFill" x1="0" y1="0" x2="1" y2="1">
        <stop offset="0" stop-color="#a8302b"/>
        <stop offset="1" stop-color="#6e1212"/>
      </linearGradient>
    </defs>
    <path d="M0 0 H620 V300 C520 170 340 50 0 44 Z" fill="#f4c993"/>
    <path d="M0 0 H620 V284 C520 150 340 38 0 28 Z" fill="#ffffff"/>
    <path d="M200 0 H620 V270 C540 150 400 40 200 0 Z" fill="url(#bandFill)"/>
  </svg>
  <div class="back__ornament" role="img" aria-label="Gold floral flourish on the maroon band"></div>
  <div class="back__name">Marlow &amp; Quince</div>
  <ul class="contact-list">
    <li><svg viewBox="0 0 14 14"><path d="M3 1 L5 1 L6 4 L4.5 5 C5.3 7 7 8.7 9 9.5 L10 8 L13 9 L13 11 C13 12 12 13 11 13 C5.5 12.5 1.5 8.5 1 3 C1 2 2 1 3 1 Z" fill="none" stroke="#2a1a1a" stroke-width="1.2"/></svg>512-555-0140</li>
    <li><svg viewBox="0 0 14 14"><rect x="1" y="5" width="12" height="7" rx="1.5" fill="#6e1212"/><rect x="3" y="2" width="8" height="4" fill="#6e1212"/></svg>512-555-0141</li>
    <li><svg viewBox="0 0 14 14"><rect x="1" y="3" width="12" height="8" rx="1" fill="#6e1212"/><path d="M1 3 L7 8 L13 3" fill="none" stroke="#fff" stroke-width="1"/></svg>info@marlowquince.com</li>
    <li><svg viewBox="0 0 14 14"><circle cx="7" cy="7" r="6" fill="#6e1212"/></svg>www.marlowquince.com</li>
  </ul>
  <div class="back__signature">Marlow &amp; Quince</div>
</section>

</body>
</html>
```